Business Card Design

We would like to re-design our business cards. Our Company - Qwinrel Turbochargers, rebuilds turbochargers and sells replacement parts. Our website is: http://www.qwinrelturbochargers-example.com
We just had our logo changed. I will attach the file. Looking for fresh new/modern business card. We like the colors red, black, white and silver. Black background looks attractive, but not a requirement. The final design should communicate reasonable/competitive prices, top quality and reliability of our products.
Updates
Project Deadline Extended
Reason: Need to finalize the info on the card. Currently working on changing address and email info. Want to make sure it is the correct one before accepting the final design. Unless, this is something that can be changed at a later time..??
Industry/Entity Type
Business
Contact Information for Business Card
QWINREL TURBOCHARGERS, LLC
20473 Harwick Lane NE
Massillon, OH 44647
Tel: +1-555-214-7390
Fax: +1-555-267-1842
info@QwinrelTurbochargers-example.com
Our current business card had the following highlights:
*We rebuild all Turbocharges for Automotive, Diesel and Industrial
*Precision Balancing and in-house turbocharger needs
*All Turbocharger replacement parts are made in USA / U.K.
Look and feel
Each slider illustrates characteristics of the customer's brand and the style your logo design should communicate.

```html
<!DOCTYPE html>
<html lang="en">
<head>
<meta charset="utf-8">
<title>Qwinrel Turbochargers – Business Card</title>
<link href="https://fonts.googleapis.com/css2?family=Arimo:wght@400;700&display=swap" rel="stylesheet">
<style>
  :root {
    --backdrop: #3a3431;
    --card-black: #141414;
    --card-edge: #0a0a0a;
    --brand-red: #e3232a;
    --text-white: #ffffff;
    --text-soft: #e6e6e6;
  }
  * { margin: 0; padding: 0; box-sizing: border-box; }
  html, body { width: 1200px; height: 780px; overflow: hidden; }
  body {
    background: var(--backdrop);
    font-family: "Arimo", Arial, sans-serif;
    position: relative;
  }
  .card {
    position: absolute;
    top: 241px;
    width: 520px;
    height: 298px;
    background: radial-gradient(ellipse at 40% 30%, #1e1e1e 0%, var(--card-black) 70%);
    border: 1px solid var(--card-edge);
    box-shadow: 0 14px 30px rgba(0,0,0,0.45);
  }
  .card--front { left: 50px; }
  .card--back { left: 630px; }

  .brand {
    display: flex;
    align-items: center;
    gap: 12px;
  }
  .brand__dot {
    width: 30px;
    height: 30px;
    border-radius: 50%;
    background: var(--brand-red);
    flex: none;
  }
  .brand__name {
    font-weight: 700;
    color: var(--text-white);
    letter-spacing: 0.5px;
    white-space: nowrap;
  }

  .card--front .brand {
    position: absolute;
    inset: 0;
    justify-content: center;
  }
  .card--front .brand__name { font-size: 30px; }

  .card--back .brand {
    position: absolute;
    left: 0;
    right: 0;
    top: 60px;
    justify-content: center;
  }
  .card--back .brand__name { font-size: 27px; }

  .contact {
    position: absolute;
    left: 0;
    right: 0;
    top: 124px;
    text-align: center;
    color: var(--text-white);
    font-size: 15px;
    line-height: 1.4;
  }
  .contact__name {
    color: var(--brand-red);
    font-size: 20px;
    font-weight: 400;
  }
  .contact__title {
    color: var(--text-soft);
    font-size: 14px;
    margin-bottom: 12px;
  }
</style>
</head>
<body>
  <section class="card card--front" aria-label="Card front">
    <div class="brand">
      <span class="brand__dot"></span>
      <span class="brand__name">Qwinrel Turbochargers</span>
    </div>
  </section>

  <section class="card card--back" aria-label="Card back">
    <div class="brand">
      <span class="brand__dot"></span>
      <span class="brand__name">Qwinrel Turbochargers</span>
    </div>
    <div class="contact">
      <p class="contact__name">Employee Name</p>
      <p class="contact__title">Managing Director</p>
      <p class="contact__phone">555-214-7390</p>
      <p class="contact__web">www.qwinrelturbochargers-example.com</p>
      <p class="contact__address">20473 Harwick Lane NE, Brellford Ohio 40219</p>
    </div>
  </section>
</body>
</html>
```